New Business Card Design Project

Use the flyer uploaded and website www.brightoakbuilders.com for inspiration.
List Our Services on Backside of business cards
Marcus Delling
Harborline Builders Inc.
Licensed General Contractors
858-471-6093

Contact Information for Business Card

Use the flyer uploaded and website www.brightoakbuilders.com for inspiration. List Our Services on Backside of business cards Marcus Delling Harborline Builders Inc. Licensed General Contractors 858-471-6093

```html
<!DOCTYPE html>
<html lang="en">
<head>
<meta charset="utf-8">
<title>Harborline Builders – Business Cards</title>
<link rel="stylesheet" href="https://fonts.googleapis.com/css2?family=Roboto:wght@400;500;700;900&display=swap">
<style>
  :root {
    --bg: #232323;
    --card: #ffffff;
    --ink: #1c1c1c;
    --red: #e3121b;
    --blue: #4a78c8;
    --rule: #222222;
    --shadow: rgba(0,0,0,0.45);
  }
  * { margin: 0; padding: 0; box-sizing: border-box; }
  html, body { width: 1200px; height: 780px; overflow: hidden; }
  body {
    background: var(--bg);
    font-family: "Roboto", Arial, sans-serif;
    color: var(--ink);
    position: relative;
  }
  .card {
    position: absolute;
    top: 235px;
    width: 540px;
    height: 310px;
    background: var(--card);
    box-shadow: 0 14px 30px var(--shadow);
  }
  .card--front { left: 40px; }
  .card--back { left: 620px; }

  /* wordmark */
  .wordmark {
    font-family: "Roboto", Arial, sans-serif;
    font-weight: 400;
    color: var(--ink);
    letter-spacing: 3px;
    text-transform: uppercase;
    display: flex;
    align-items: center;
    gap: 10px;
  }
  .wordmark__square { width: 12px; height: 12px; background: var(--ink); flex: none; }

  /* front */
  .front__brand { position: absolute; left: 0; top: 0; width: 270px; height: 310px; }
  .front__brand .wordmark { position: absolute; left: 32px; top: 78px; font-size: 19px; }
  .front__company { position: absolute; left: 0; width: 270px; bottom: 46px; text-align: center; font-size: 14px; }
  .front__divider { position: absolute; left: 276px; top: 84px; width: 1px; height: 150px; background: var(--rule); }
  .front__contact { position: absolute; left: 300px; top: 70px; }
  .contact__name { color: var(--red); font-weight: 900; font-size: 30px; letter-spacing: 0.5px; text-transform: uppercase; line-height: 1; }
  .contact__title { font-size: 14px; margin-top: 8px; }
  .contact__list { list-style: none; margin-top: 14px; }
  .contact__item { display: flex; align-items: center; gap: 8px; font-size: 13.5px; font-weight: 500; margin-bottom: 7px; }
  .contact__icon { width: 13px; height: 13px; flex: none; }

  /* back */
  .back__brand { position: absolute; top: 48px; width: 100%; display: flex; justify-content: center; }
  .back__brand .wordmark { font-size: 22px; }
  .back__guarantee { position: absolute; top: 112px; width: 100%; text-align: center; color: var(--red); font-weight: 900; font-size: 15px; text-transform: uppercase; }
  .back__heading { position: absolute; top: 136px; width: 100%; text-align: center; color: var(--blue); font-weight: 900; font-size: 14px; text-transform: uppercase; }
  .services { position: absolute; top: 168px; left: 22px; right: 22px; text-align: center; font-size: 11.5px; font-weight: 500; line-height: 22px; }
  .service { white-space: nowrap; margin: 0 3px; }
  .service__tick { width: 9px; height: 9px; vertical-align: -1px; margin-right: 3px; }
</style>
</head>
<body>

<section class="card card--front" aria-label="Business card front">
  <div class="front__brand">
    <div class="wordmark"><span class="wordmark__square"></span>Harborline Builders</div>
    <p class="front__company">Harborline Builders Inc.</p>
  </div>
  <div class="front__divider"></div>
  <div class="front__contact">
    <h1 class="contact__name">Marcus Delling</h1>
    <p class="contact__title">Licensed General Contractors</p>
    <ul class="contact__list">
      <li class="contact__item">
        <svg class="contact__icon" viewBox="0 0 24 24"><path fill="#e3121b" d="M6.6 10.8a15.1 15.1 0 0 0 6.6 6.6l2.2-2.2a1 1 0 0 1 1-.25 11.4 11.4 0 0 0 3.6.57 1 1 0 0 1 1 1V20a1 1 0 0 1-1 1A17 17 0 0 1 3 4a1 1 0 0 1 1-1h3.5a1 1 0 0 1 1 1c0 1.25.2 2.45.57 3.57a1 1 0 0 1-.25 1z"/></svg>
        858-471-6093
      </li>
      <li class="contact__item">
        <svg class="contact__icon" viewBox="0 0 24 24"><rect x="2" y="5" width="20" height="14" rx="2" fill="#e3121b"/><path d="M3 6l9 7 9-7" fill="none" stroke="#fff" stroke-width="2"/></svg>
        info@brightoakbuilders.com
      </li>
      <li class="contact__item">
        <svg class="contact__icon" viewBox="0 0 24 24"><circle cx="12" cy="12" r="10" fill="#e3121b"/><path d="M2 12h20M12 2c3 3 3 17 0 20M12 2c-3 3-3 17 0 20" fill="none" stroke="#fff" stroke-width="1.5"/></svg>
        www.brightoakbuilders.com
      </li>
    </ul>
  </div>
</section>

<section class="card card--back" aria-label="Business card back">
  <div class="back__brand">
    <div class="wordmark"><span class="wordmark__square"></span>Harborline Builders</div>
  </div>
  <p class="back__guarantee">Our services are 100% guaranteed</p>
  <p class="back__heading">Specializing in:</p>
  <p class="services">
    <span class="service"><svg class="service__tick" viewBox="0 0 10 10"><circle cx="5" cy="5" r="4.3" fill="none" stroke="#e3121b"/><path d="M2.8 5.2l1.5 1.5 3-3.2" fill="none" stroke="#e3121b" stroke-width="1.2"/></svg>Remodel: Kitchen &amp; Bath</span>
    <span class="service"><svg class="service__tick" viewBox="0 0 10 10"><circle cx="5" cy="5" r="4.3" fill="none" stroke="#e3121b"/><path d="M2.8 5.2l1.5 1.5 3-3.2" fill="none" stroke="#e3121b" stroke-width="1.2"/></svg>Painting: Interior &amp; Exterior</span>
    <span class="service"><svg class="service__tick" viewBox="0 0 10 10"><circle cx="5" cy="5" r="4.3" fill="none" stroke="#e3121b"/><path d="M2.8 5.2l1.5 1.5 3-3.2" fill="none" stroke="#e3121b" stroke-width="1.2"/></svg>Flooring: Carpet, Vinyl, Wood</span><br>
    <span class="service"><svg class="service__tick" viewBox="0 0 10 10"><circle cx="5" cy="5" r="4.3" fill="none" stroke="#e3121b"/><path d="M2.8 5.2l1.5 1.5 3-3.2" fill="none" stroke="#e3121b" stroke-width="1.2"/></svg>Window &amp; Door Replacement</span>
    <span class="service"><svg class="service__tick" viewBox="0 0 10 10"><circle cx="5" cy="5" r="4.3" fill="none" stroke="#e3121b"/><path d="M2.8 5.2l1.5 1.5 3-3.2" fill="none" stroke="#e3121b" stroke-width="1.2"/></svg>Plumbing: Repairs &amp; Upgrades</span>
    <span class="service"><svg class="service__tick" viewBox="0 0 10 10"><circle cx="5" cy="5" r="4.3" fill="none" stroke="#e3121b"/><path d="M2.8 5.2l1.5 1.5 3-3.2" fill="none" stroke="#e3121b" stroke-width="1.2"/></svg>Energy-Efficient Upgrades</span><br>
    <span class="service"><svg class="service__tick" viewBox="0 0 10 10"><circle cx="5" cy="5" r="4.3" fill="none" stroke="#e3121b"/><path d="M2.8 5.2l1.5 1.5 3-3.2" fill="none" stroke="#e3121b" stroke-width="1.2"/></svg>Deck &amp; Patio Construction</span>
    <span class="service"><svg class="service__tick" viewBox="0 0 10 10"><circle cx="5" cy="5" r="4.3" fill="none" stroke="#e3121b"/><path d="M2.8 5.2l1.5 1.5 3-3.2" fill="none" stroke="#e3121b" stroke-width="1.2"/></svg>Water &amp; Mold Damage</span>
    <span class="service"><svg class="service__tick" viewBox="0 0 10 10"><circle cx="5" cy="5" r="4.3" fill="none" stroke="#e3121b"/><path d="M2.8 5.2l1.5 1.5 3-3.2" fill="none" stroke="#e3121b" stroke-width="1.2"/></svg>Garage Renovation</span>
  </p>
</section>

</body>
</html>
```